Etiketten für Olivenöl-Intensivcreme
Zielgruppe
Wir produzieren Bio-Food, u.a. Wein und Olivenöl. Jetzt soll eine Olivenöl-Intensivcreme im Bereich Kosmetik auf dem Markt platziert werden. Unsere Zielgruppe hat ein sehr breites Altersspektrum (jung bis alt), ist naturverbunden, tierlieb, gebildet, kritisch-reflektierend, weiß gute Qualität zu schätzen, ist überwiegend weiblich. Die Olivenöl-Intensivcreme hat eine sehr breite Verwendung und soll sich als 'Allzweckwaffe' in jedem Haushalt etablieren (Babyhaut-Pflege, Lippenpflege, Ganzkörperpflege, Hand-Schutzcreme etc.).
Aufgabenstellung
Die Creme soll heißen: Velamira (es könnte z.B. der Buchstabe 'O' durch eine Olive ersetzt werden). Es gibt zwei Etikette (Deckeloberseite der Metalldose und auf dem Boden). Der Durchmesser der Etikette ist jeweils 5,5 cm. Die Deckelunterseite gilt reinen Pflichtangaben. Im Dateidownloadbereich sind die Textvorgaben für die Etikette. MUT zur Farbe! Wir sind NICHT brav und angepasst! Orange kann Akzente setzen bzw. für Aufmerksamkeit im Regal sorgen.

```html
<!DOCTYPE html>
<html lang="de">
<head>
<meta charset="utf-8">
<title>Velamira – Etiketten Olivenöl-Intensivcreme</title>
<link rel="stylesheet" href="https://fonts.googleapis.com/css2?family=Oswald:wght@300;400;500&family=Signika:wght@600&display=swap">
<style>
  :root {
    --paper: #ffffff;
    --rim: #111111;
    --olive-green: #5b8a2a;
    --deep-green: #256b17;
    --olive-fruit: #9cbf2c;
    --accent-orange: #e07a12;
    --accent-red: #d64a12;
    --splash-light: #f6a23c;
    --splash-dark: #b9520a;
    --tree-grey: #b9b9b9;
    --tree-faint: #ececec;
    --claim-grey: #8a8a8a;
  }
  html, body {
    margin: 0;
    padding: 0;
    width: 1200px;
    height: 948px;
    overflow: hidden;
    background: var(--paper);
  }
  .label-sheet { display: block; width: 1200px; height: 948px; }
  .label-rim { fill: var(--paper); stroke: var(--rim); stroke-width: 2; }
  .brand-name {
    font-family: "Oswald", sans-serif;
    font-weight: 500;
    font-size: 54px;
    fill: var(--olive-green);
  }
  .brand-dot { fill: var(--olive-fruit); }
  .product-name {
    font-family: "Oswald", sans-serif;
    font-weight: 300;
    font-size: 25px;
    fill: var(--accent-orange);
  }
  .category-box { fill: var(--deep-green); }
  .category-name {
    font-family: "Oswald", sans-serif;
    font-weight: 400;
    font-size: 27px;
    fill: #ffffff;
  }
  .claim-arc {
    font-family: "Signika", sans-serif;
    font-weight: 600;
    font-size: 13.5px;
    fill: var(--claim-grey);
  }
  .claim-arc--accent { fill: var(--accent-red); }
  .claim-list {
    font-family: "Signika", sans-serif;
    font-weight: 600;
    font-size: 15px;
    fill: var(--claim-grey);
  }
  .claim-bullet { fill: var(--accent-orange); }
  .tree-mark { fill: var(--tree-grey); }
  .tree-backdrop { fill: var(--tree-faint); }
  .oil-splash { fill: url(#splashTone); }
  .oil-drip { fill: none; stroke: url(#splashTone); stroke-width: 7; stroke-linecap: round; }
</style>
</head>
<body>
<svg class="label-sheet" viewBox="0 0 1200 948" xmlns="http://www.w3.org/2000/svg">
  <defs>
    <linearGradient id="splashTone" x1="0" y1="0" x2="1" y2="1">
      <stop offset="0" stop-color="var(--splash-light)"/>
      <stop offset="0.55" stop-color="#ea8a20"/>
      <stop offset="1" stop-color="var(--splash-dark)"/>
    </linearGradient>
    <clipPath id="labelArea"><circle cx="0" cy="0" r="193"/></clipPath>
    <path id="claimPath" d="M -22,178 A 178 178 0 0 0 176,-30"/>
    <path id="claimPathWide" d="M -22,178 A 178 178 0 0 0 162,-75"/>
  </defs>

  <!-- Label 1: lid top, arc claim -->
  <g class="label label--arc" transform="translate(385,289)">
    <circle class="label-rim" r="194"/>
    <g clip-path="url(#labelArea)">
      <path class="oil-splash" role="img" aria-label="Orangefarbener Olivenöl-Spritzer am linken Rand"
        d="M -150,-175 C -110,-130 -150,-95 -122,-62 C -100,-30 -142,8 -110,42 C -82,72 -62,112 -50,142 C -40,162 -28,178 -18,200 L -200,200 L -200,-200 Z"/>
      <path class="oil-drip" role="img" aria-label="Öltropfen oben rechts"
        d="M 70,-162 C 110,-150 130,-125 145,-85 L 152,-62"/>
    </g>
    <rect class="tree-mark" role="img" aria-label="Kleines Olivenbaum-Symbol" x="-32" y="-170" width="64" height="55" rx="26"/>
    <circle class="brand-dot" cx="-84" cy="-30" r="30"/>
    <text class="brand-name" x="-46" y="-6">Velamira</text>
    <text class="product-name" x="-124" y="38" textLength="260" lengthAdjust="spacingAndGlyphs">OLIVENÖL-INTENSIVCREME</text>
    <rect class="category-box" x="-62" y="48" width="195" height="38"/>
    <text class="category-name" x="-55" y="79" textLength="181" lengthAdjust="spacingAndGlyphs">NATURKOSMETIK</text>
    <text class="claim-arc"><textPath href="#claimPath">Bio-Olive • Vegan • Pflege - und Schutzcreme</textPath></text>
  </g>

  <!-- Label 2: lid top, bullet claims -->
  <g class="label label--list" transform="translate(843,289)">
    <circle class="label-rim" r="194"/>
    <g clip-path="url(#labelArea)">
      <path class="oil-splash" role="img" aria-label="Orangefarbener Olivenöl-Spritzer am linken Rand"
        d="M -150,-175 C -110,-130 -150,-95 -122,-62 C -100,-30 -142,8 -110,42 C -82,72 -62,112 -50,142 C -40,162 -28,178 -18,200 L -200,200 L -200,-200 Z"/>
      <path class="oil-drip" role="img" aria-label="Öltropfen oben rechts"
        d="M 65,-160 C 105,-148 128,-122 142,-82 L 150,-60"/>
    </g>
    <rect class="tree-mark" role="img" aria-label="Kleines Olivenbaum-Symbol" x="-45" y="-168" width="90" height="70" rx="30"/>
    <circle class="brand-dot" cx="-108" cy="-36" r="32"/>
    <text class="brand-name" x="-68" y="-2">Velamira</text>
    <text class="product-name" x="-112" y="43" textLength="229" lengthAdjust="spacingAndGlyphs">OLIVENÖL-INTENSIVCREME</text>
    <rect class="category-box" x="-60" y="51" width="177" height="30"/>
    <text class="category-name" x="-52" y="76" font-size="23" textLength="161" lengthAdjust="spacingAndGlyphs">NATURKOSMETIK</text>
    <text class="claim-list" x="-94" y="104"><tspan class="claim-bullet">• </tspan>Pflege - und Schutzcreme</text>
    <text class="claim-list" x="-32" y="124"><tspan class="claim-bullet">• </tspan>Bio-Olive</text>
    <text class="claim-list" x="6" y="146"><tspan class="claim-bullet">• </tspan>Vegan</text>
  </g>

  <!-- Label 3: lid top, large tree backdrop, accent arc claim -->
  <g class="label label--backdrop" transform="translate(612,652)">
    <circle class="label-rim" r="194"/>
    <g clip-path="url(#labelArea)">
      <rect class="tree-backdrop" role="img" aria-label="Großer, blasser Olivenbaum im Hintergrund" x="-146" y="-166" width="284" height="150" rx="70"/>
      <path class="oil-splash" role="img" aria-label="Orangefarbener Olivenöl-Spritzer am linken Rand"
        d="M -150,-175 C -110,-130 -150,-95 -122,-62 C -100,-30 -142,8 -110,42 C -82,72 -62,112 -50,142 C -40,162 -28,178 -18,200 L -200,200 L -200,-200 Z"/>
      <path class="oil-drip" role="img" aria-label="Öltropfen oben rechts"
        d="M 78,-157 C 115,-145 135,-118 148,-80 L 155,-58"/>
    </g>
    <circle class="brand-dot" cx="-96" cy="-22" r="32"/>
    <text class="brand-name" x="-56" y="12">Velamira</text>
    <text class="product-name" x="-112" y="48" textLength="230" lengthAdjust="spacingAndGlyphs">OLIVENÖL-INTENSIVCREME</text>
    <rect class="category-box" x="-48" y="57" width="166" height="32"/>
    <text class="category-name" x="-42" y="83" font-size="25" textLength="154" lengthAdjust="spacingAndGlyphs">NATURKOSMETIK</text>
    <text class="claim-arc claim-arc--accent"><textPath href="#claimPathWide">Bio-Olive • Vegan • Pflege - und Schutzcreme</textPath></text>
  </g>
</svg>
</body>
</html>
```